Very visible CoWorking Building Sign overlooking downtown LA and 110 freeway

Our building is drab but very visible and in the best location. We need a great sign for our monolith that overlooks downtown LA and the 100 freeway. We are a new CoWorking business and would like to have a few things we do on the sign: private offices, virtual offices, CoWorking Lounge. Everything we have seen is ho-hum. Can you get us noticed? We need people to know what we do and that we are here but in a creative, professional, unique sign.
Target Market(s)
People who have a business in DTLA, remote workers and those who work from home who need a professional address.
Requirements
Must have
- Our logo (which can be somewhat reimagined) which has our address 2417 on it. The three things we focus on: Private Offices, Virtual Offices, CoWorking Lounge. Incorporate some Navy. Readable from several hundred feet away.
Nice to have
- Mural feel? Something inspirational in this crazy COVID times? Graphics? Color block. I like the idea of decorative but it has to be readable as a building sign. The same with the use of colors. Our colors are grays and navy but with a pop of the chartreuse (we have 2 velvet chartreuse chairs in the space). Helpful to view our website: Harborview2417.com.
Should not have
- Not too graffiti. Keep it professional but unique and wow.

```html
<!DOCTYPE html>
<html lang="en">
<head>
<meta charset="utf-8">
<title>2417 Harborview – Building Sign</title>
<link href="https://fonts.googleapis.com/css2?family=Tinos:wght@400;700&display=swap" rel="stylesheet">
<style>
  :root {
    --navy: #0e2a4f;
    --chartreuse: #9ac83c;
    --blue: #0b63b5;
    --white: #ffffff;
    --backdrop: #bdbdbd;
  }
  html, body {
    margin: 0;
    padding: 0;
    width: 1200px;
    height: 1097px;
    overflow: hidden;
    background: var(--backdrop);
  }
  .sign {
    position: absolute;
    left: 290px;
    top: 33px;
    width: 620px;
    height: 1030px;
    background: var(--navy);
    overflow: hidden;
    font-family: "Tinos", "Times New Roman", serif;
  }
  .sign__wordmark {
    position: absolute;
    left: 0;
    width: 100%;
    top: 118px;
    margin: 0;
    text-align: center;
    color: var(--chartreuse);
    font-weight: 700;
    font-size: 54px;
    letter-spacing: 1px;
    line-height: 1;
  }
  .sign__rule {
    position: absolute;
    left: 253px;
    top: 213px;
    width: 113px;
    height: 6px;
    background: var(--white);
  }
  .service {
    position: absolute;
    left: 70px;
    width: 530px;
    height: 172px;
  }
  .service__icon {
    position: absolute;
    left: 0;
    top: 0;
    width: 166px;
    height: 166px;
    border-radius: 50%;
    background: var(--chartreuse);
    border: 3px solid var(--white);
  }
  .service__label {
    position: absolute;
    left: 197px;
    top: 40px;
    margin: 0;
    color: var(--white);
    font-weight: 700;
    font-size: 41px;
    line-height: 45px;
    letter-spacing: 0.5px;
    white-space: nowrap;
  }
  .service--private { top: 246px; }
  .service--virtual { top: 442px; }
  .service--lounge  { top: 638px; }
  .divider {
    position: absolute;
    left: 283px;
    width: 179px;
    height: 1px;
    background: var(--white);
  }
  .divider--first  { top: 429px; }
  .divider--second { top: 628px; }
  .sign__wave {
    position: absolute;
    left: 0;
    top: 0;
  }
  .sign__phone {
    position: absolute;
    left: 0;
    width: 100%;
    top: 896px;
    margin: 0;
    text-align: center;
    color: var(--white);
    font-weight: 700;
    font-size: 100px;
    letter-spacing: -2px;
    line-height: 1;
  }
</style>
</head>
<body>
  <main class="sign">
    <h1 class="sign__wordmark">2417 HARBORVIEW</h1>
    <div class="sign__rule"></div>

    <section class="service service--private">
      <div class="service__icon" role="img" aria-label="Line icon of a private office desk with chair, lamp and picture frame"></div>
      <h2 class="service__label">PRIVATE<br>OFFICES</h2>
    </section>
    <div class="divider divider--first"></div>

    <section class="service service--virtual">
      <div class="service__icon" role="img" aria-label="Line icon of a reception desk with mail envelope and plant"></div>
      <h2 class="service__label">VIRTUAL<br>OFFICES</h2>
    </section>
    <div class="divider divider--second"></div>

    <section class="service service--lounge">
      <div class="service__icon" role="img" aria-label="Line icon of people talking at a shared table"></div>
      <h2 class="service__label">COWORKING<br>LOUNGE</h2>
    </section>

    <svg class="sign__wave" width="620" height="1030" viewBox="0 0 620 1030" aria-hidden="true">
      <path d="M0,772 C200,880 420,870 620,785 L620,1030 L0,1030 Z" fill="var(--chartreuse)"/>
      <path d="M0,781 C200,889 420,879 620,794 L620,1030 L0,1030 Z" fill="var(--navy)"/>
      <path d="M0,792 C200,880 440,875 620,806 L620,1030 L0,1030 Z" fill="var(--blue)"/>
      <path d="M0,828 C200,884 430,870 620,810 L620,1030 L0,1030 Z" fill="var(--navy)"/>
      <path d="M0,834 C200,886 430,872 620,814 L620,1030 L0,1030 Z" fill="var(--white)"/>
      <path d="M0,840 C200,892 430,880 620,838 L620,1030 L0,1030 Z" fill="var(--blue)"/>
      <path d="M0,846 C200,894 430,884 620,866 L620,1030 L0,1030 Z" fill="var(--chartreuse)"/>
    </svg>

    <p class="sign__phone">310.555.2417</p>
  </main>
</body>
</html>
```